Business Card Design

Self contained holiday cottage, situated on T7V cycle trail. Catered stays available. On the back my Velmar Plum business-design sent-add gate sales , able to overnight courier anywhere in NZ.change phone number 0274861537 add email lampandwillow@fernpost.co.nz. Open to any suggestions-need folks to know cottage available,100yr old-step back in time, on T7V cycle trail

Industry/Entity Type

Business

Contact Information for Business Card

Rod & Saddle Holiday Cottage5540 Highway 83Kurow 9498Ph 027 2290260email lampandwillow@fernpost.co.nz

```html
<!DOCTYPE html>
<html lang="en">
<head>
<meta charset="utf-8">
<title>Lamp &amp; Willow Holiday Cottage – Business Cards</title>
<link rel="stylesheet" href="https://fonts.googleapis.com/css2?family=Oswald:wght@400;500;700&family=Playball&display=swap">
<style>
  :root {
    --stage: #161616;
    --card: #f7f7f6;
    --maroon: #8a4b46;
    --maroon-deep: #5e1a1c;
    --leaf: #6fa552;
    --forest: #2e4a2c;
    --ink: #4a4a4a;
  }
  * { box-sizing: border-box; margin: 0; padding: 0; }
  html, body { width: 1200px; height: 871px; overflow: hidden; }
  body {
    background: var(--stage);
    font-family: "Oswald", sans-serif;
    position: relative;
  }
  .card {
    position: absolute;
    width: 600px;
    height: 343px;
    background: var(--card);
    box-shadow: 0 12px 30px rgba(0,0,0,.6);
  }
  /* Produce card */
  .card--produce { left: 40px; top: 50px; }
  .produce-contacts {
    position: absolute; left: 372px; top: 30px;
    list-style: none; font-weight: 500; font-size: 14px; color: var(--ink);
  }
  .produce-contacts li, .cottage-contacts li {
    display: flex; align-items: center; gap: 8px; line-height: 22px;
  }
  .icon { width: 13px; height: 13px; fill: var(--maroon); flex: none; }
  .produce-title {
    position: absolute; left: 48px; top: 112px; display: flex; align-items: flex-end; gap: 6px;
  }
  .produce-tagline {
    font-family: "Playball", cursive; color: var(--leaf);
    font-size: 24px; line-height: 22px;
  }
  .produce-name {
    font-weight: 700; font-size: 40px; letter-spacing: 2px; color: var(--maroon); line-height: 44px;
  }
  .produce-photo {
    position: absolute; left: 380px; top: 120px; width: 190px; height: 130px;
    border-radius: 40% 40% 45% 45%;
    background: radial-gradient(circle at 35% 45%, #8e2a2e 0%, var(--maroon-deep) 55%, #2a0a0c 100%);
  }
  .produce-note {
    position: absolute; left: 48px; bottom: 52px;
    font-weight: 700; font-size: 18px; letter-spacing: 1px; color: var(--maroon);
  }
  /* Cottage card */
  .card--cottage { left: 560px; top: 470px; }
  .cottage-mark {
    position: absolute; left: 0; right: 0; top: 60px; text-align: center;
  }
  .cottage-mark .dot {
    display: inline-block; width: 44px; height: 44px; border-radius: 50%;
    background: var(--forest); margin-bottom: 14px;
  }
  .cottage-name {
    font-weight: 500; font-size: 30px; line-height: 38px; letter-spacing: 2px;
    color: var(--forest); text-transform: uppercase;
  }
  .cottage-contacts {
    position: absolute; left: 30px; right: 30px; bottom: 40px;
    list-style: none; display: flex; justify-content: space-between;
    font-weight: 500; font-size: 15px; color: var(--ink);
  }
</style>
</head>
<body>

<section class="card card--produce">
  <ul class="produce-contacts">
    <li><svg class="icon" viewBox="0 0 16 16"><path d="M3 1h3l1.5 4-2 1.5a9 9 0 0 0 4 4L11 8.5l4 1.5v3a2 2 0 0 1-2 2A12 12 0 0 1 1 3a2 2 0 0 1 2-2z"/></svg>0274861537</li>
    <li><svg class="icon" viewBox="0 0 16 16"><path d="M1 3h14v10H1z M1 3l7 6 7-6" fill="none" stroke="#8a4b46" stroke-width="1.6"/></svg>lampandwillow@fernpost.co.nz</li>
    <li><svg class="icon" viewBox="0 0 16 16"><path d="M8 0a5.5 5.5 0 0 0-5.5 5.5C2.5 10 8 16 8 16s5.5-6 5.5-10.5A5.5 5.5 0 0 0 8 0zm0 8a2.5 2.5 0 1 1 0-5 2.5 2.5 0 0 1 0 5z"/></svg>3172 Highway 61 Velmar</li>
  </ul>
  <div class="produce-title">
    <div class="produce-tagline">Velmar<br>Spray free</div>
    <div class="produce-name">PLUMS</div>
  </div>
  <div class="produce-photo" role="img" aria-label="Photo of two ripe dark red fruit joined by their stems"></div>
  <p class="produce-note">Able to overnight courier anywhere in NZ</p>
</section>

<section class="card card--cottage">
  <div class="cottage-mark">
    <span class="dot"></span>
    <div class="cottage-name">Lamp &amp; Willow<br>Holiday Cottage</div>
  </div>
  <ul class="cottage-contacts">
    <li><svg class="icon" viewBox="0 0 16 16"><path d="M8 0a5.5 5.5 0 0 0-5.5 5.5C2.5 10 8 16 8 16s5.5-6 5.5-10.5A5.5 5.5 0 0 0 8 0zm0 8a2.5 2.5 0 1 1 0-5 2.5 2.5 0 0 1 0 5z"/></svg>3172 Highway 61 Velmar 9316</li>
    <li><svg class="icon" viewBox="0 0 16 16"><path d="M3 1h3l1.5 4-2 1.5a9 9 0 0 0 4 4L11 8.5l4 1.5v3a2 2 0 0 1-2 2A12 12 0 0 1 1 3a2 2 0 0 1 2-2z"/></svg>027 4861537</li>
    <li><svg class="icon" viewBox="0 0 16 16"><path d="M1 3h14v10H1z M1 3l7 6 7-6" fill="none" stroke="#8a4b46" stroke-width="1.6"/></svg>lampandwillow@fernpost.co.nz</li>
  </ul>
</section>

</body>
</html>
```